Stationery Design Project

I need a design that is simple, clean and modern, in square style, bold font.
The majority of the design needs to be White and Black with a splash of Red colour.
I would like a design for business cards and letter heads with the following information.
Name, Title, Phone, Fax, Email, Website and company ABN number

Target Market(s)

25 to 65 years old real estate clients

Industry/Entity Type

Business

Requirements
Must have
• All designs must incorporate Company Logo, Name, Title, Phone, Fax, Email, Website and company ABN number

```html
<!DOCTYPE html>
<html lang="en">
<head>
<meta charset="utf-8">
<title>Ashford Lane Real Estate – Business Card</title>
<link rel="stylesheet" href="https://fonts.googleapis.com/css2?family=Lato:wght@400;700&display=swap">
<style>
  :root {
    --page-bg: #e6e8ea;
    --card-white: #ffffff;
    --card-black: #2b2a2a;
    --ink: #262626;
    --ink-soft: #3a3a3a;
    --rule: #3a3a3a;
    --accent-red: #e0202a;
  }
  * { box-sizing: border-box; margin: 0; padding: 0; }
  html, body {
    width: 1200px; height: 960px; overflow: hidden;
    background: var(--page-bg);
    font-family: "Lato", Arial, sans-serif;
    color: var(--ink);
  }
  .sheet {
    width: 1200px; height: 960px;
    display: flex; flex-direction: column;
    align-items: center; justify-content: center; gap: 60px;
  }
  .card {
    position: relative;
    width: 700px; height: 400px;
    box-shadow: 0 6px 20px rgba(0,0,0,.18);
  }
  /* Front */
  .card--front { background: var(--card-white); }
  .brand {
    position: absolute; top: 44px; right: 40px;
    display: flex; align-items: center; gap: 12px;
  }
  .brand__mark { width: 14px; height: 14px; background: var(--accent-red); }
  .brand__name {
    font-weight: 700; font-size: 30px; letter-spacing: 1px;
    color: var(--ink); text-transform: uppercase;
  }
  .person {
    position: absolute; left: 40px; top: 196px; width: 620px;
  }
  .person__name { font-size: 34px; font-weight: 400; line-height: 1; padding-bottom: 10px;
    border-bottom: 1.5px solid var(--rule); }
  .person__title { font-size: 19px; color: var(--ink-soft); padding: 8px 0 12px;
    border-bottom: 1.5px solid var(--rule); width: 330px; }
  .contacts {
    position: absolute; left: 40px; top: 306px;
    list-style: none; font-size: 20px; color: var(--ink-soft);
  }
  .contacts li { display: flex; align-items: center; gap: 14px; height: 26px; }
  .contacts svg { width: 18px; height: 18px; fill: none; stroke: var(--accent-red); stroke-width: 1.8; }
  .company-meta {
    position: absolute; left: 420px; top: 268px;
    font-size: 16px; line-height: 22px; color: var(--ink-soft);
  }
  .company-meta__web { color: var(--accent-red); font-weight: 700; }
  /* Back */
  .card--back { background: var(--card-black); display: flex; align-items: center; justify-content: center; }
  .brand-plate {
    width: 440px; height: 150px; background: var(--card-white);
    border-radius: 18px;
    display: flex; align-items: center; justify-content: center; gap: 14px;
  }
  .brand-plate .brand__name { font-size: 32px; }
</style>
</head>
<body>
<main class="sheet">
  <section class="card card--front" aria-label="Business card front">
    <div class="brand">
      <span class="brand__mark"></span>
      <span class="brand__name">Ashford Lane Real Estate</span>
    </div>
    <div class="person">
      <h1 class="person__name">Leona Hartley</h1>
      <p class="person__title">Operation Manager</p>
    </div>
    <ul class="contacts">
      <li>
        <svg viewBox="0 0 20 20" aria-hidden="true"><rect x="2" y="2" width="16" height="16" rx="2"/><rect x="5" y="5" width="4" height="10"/><path d="M12 6h3M12 9h3M12 12h3"/></svg>
        (221) 44 210 63 18
      </li>
      <li>
        <svg viewBox="0 0 20 20" aria-hidden="true"><rect x="5" y="2" width="10" height="5"/><rect x="2" y="7" width="16" height="7" rx="1"/><rect x="5" y="12" width="10" height="6"/></svg>
        (221) 44 210 63 27
      </li>
      <li>
        <svg viewBox="0 0 20 20" aria-hidden="true"><rect x="2" y="4" width="16" height="12"/><path d="M2 4l8 7 8-7M2 16l6-6M18 16l-6-6"/></svg>
        name@ashford-lane.com
      </li>
    </ul>
    <div class="company-meta">
      <p>ABN 123456789</p>
      <p class="company-meta__web">www.ashford-lane.com</p>
    </div>
  </section>

  <section class="card card--back" aria-label="Business card back">
    <div class="brand-plate">
      <span class="brand__mark"></span>
      <span class="brand__name">Ashford Lane Real Estate</span>
    </div>
  </section>
</main>
</body>
</html>
```